Brindlewick Solutions Ltd

I'd like to create a company letterhead for the attached logo in word format.

I'd like to emphasis the icon in large translucent state from the left corner and ensure that the letterhead colouring matches the colour palette of the current logo with a contrast so it's clear to see. I've attached a copy of our sister company page on the app for reference.

```html
<!DOCTYPE html>
<html lang="en">
<head>
<meta charset="utf-8">
<title>Brindlewick Solutions Ltd — Letterhead</title>
<link href="https://fonts.googleapis.com/css2?family=Arimo:wght@400;700&family=Mulish:wght@700&display=swap" rel="stylesheet">
<style>
  :root {
    --backdrop: #e2e2e2;
    --paper: #ffffff;
    --teal: #00bda7;
    --ink: #555555;
    --on-teal: #ffffff;
  }
  * { box-sizing: border-box; margin: 0; padding: 0; }
  html, body {
    width: 1200px; height: 1200px; overflow: hidden;
    background: var(--backdrop);
  }
  .letterhead {
    position: absolute; left: 233px; top: 81px;
    width: 734px; height: 1038px;
    background: var(--paper);
    box-shadow: 1px 2px 3px rgba(0,0,0,0.25);
    font-family: "Arimo", Arial, sans-serif;
    color: var(--ink);
  }
  .header-band {
    position: absolute; left: 0; top: 42px;
    width: 458px; height: 67px;
    background: var(--teal);
    color: var(--on-teal);
    font-size: 11.4px;
    padding: 18px 0 0 37px;
  }
  .header-band .address { line-height: 16px; }
  .contact-row { display: flex; align-items: center; line-height: 16px; }
  .contact-row .item { display: flex; align-items: center; margin-right: 9px; }
  .contact-row svg { width: 10px; height: 10px; margin-right: 6px; fill: var(--on-teal); }
  .brand-dot {
    position: absolute; left: 478px; top: 57px;
    width: 34px; height: 34px; border-radius: 50%;
    background: var(--teal);
  }
  .brand-name {
    position: absolute; left: 524px; top: 52px;
    color: var(--teal);
    font-size: 24px; line-height: 26px;
  }
  .brand-name .sub { display: block; font-size: 13px; line-height: 17px; }
  .greeting {
    position: absolute; left: 67px; top: 317px;
    font-family: "Mulish", "Century Gothic", sans-serif;
    font-weight: 700; font-size: 17px;
  }
  .body-copy {
    position: absolute; left: 66px; top: 367px;
    width: 604px;
    font-size: 12.4px; line-height: 15.1px;
  }
  .body-copy p { margin-bottom: 12.9px; }
  .closing {
    position: absolute; left: 67px; top: 678px;
    font-family: "Mulish", "Century Gothic", sans-serif;
    font-weight: 700; font-size: 10px;
  }
  .signature {
    position: absolute; left: 85px; top: 726px;
    font-size: 17px; letter-spacing: -0.8px;
  }
</style>
</head>
<body>
  <main class="letterhead">
    <header>
      <div class="header-band">
        <div class="address">Your address, city, state, ZIP 0000</div>
        <div class="contact-row">
          <span class="item">
            <svg viewBox="0 0 24 24" aria-hidden="true"><path d="M6.6 10.8c1.4 2.8 3.8 5.1 6.6 6.6l2.2-2.2c.3-.3.7-.4 1-.2 1.1.4 2.3.6 3.6.6.6 0 1 .4 1 1V20c0 .6-.4 1-1 1C10.6 21 3 13.4 3 4c0-.6.4-1 1-1h3.5c.6 0 1 .4 1 1 0 1.3.2 2.5.6 3.6.1.3 0 .7-.2 1z"/></svg>
            555-017-3842
          </span>
          <span class="item">
            <svg viewBox="0 0 24 24" aria-hidden="true"><path d="M2 5h20v14H2z M2 5l10 8 10-8" fill="none" stroke="#fff" stroke-width="2"/></svg>
            hello@brindlewick.co
          </span>
          <span class="item">
            <svg viewBox="0 0 24 24" aria-hidden="true"><circle cx="12" cy="12" r="9" fill="none" stroke="#fff" stroke-width="2"/><path d="M3 12h18M12 3c3 3 3 15 0 18M12 3c-3 3-3 15 0 18" fill="none" stroke="#fff" stroke-width="1.6"/></svg>
            www.brindlewick.co
          </span>
        </div>
      </div>
      <div class="brand-dot" aria-hidden="true"></div>
      <div class="brand-name">Brindlewick<span class="sub">Solutions Ltd</span></div>
    </header>

    <h1 class="greeting">Dear Mr. Halloway,</h1>

    <section class="body-copy">
      <p>Lorem ipsum dolor sit amet, consectetuer adipiscing elit, sed diam nonmmy nibh euismod tincidunt ut laor eet dolore magna aliquam erat volutpat. Ut wisi enim ad minim veniam, quis nostrud exerci tationmcorper suscipit lobortis nisl ut aliquip ex ea commodo consequat. Duis autem vel eum iriure dolor in hendrerit in vulputate velit esse molestie consequat, vel illum dolore eu feugiat</p>
      <p>Rorem ipsum dolor sit amet, consectetuer adipiscing elit, sed diam nonmmy nibh euismod tincidunt ut laor eet dolore magna aliquam erat volutpat. Ut wisi enim ad minim veniam, quis nostrud exerci tationmcorper suscipit lobortis nisl ut aliquip ex ea commodo consequat. Duis autem vel eum iriure dolor in hendrerit in vulputate velit esse molest</p>
      <p>Dorem ipsum dolor sit amet, consectetuer adipiscing elit, sed diam nonmmy nibh euismod tincidunt ut laor eet dolore magna aliquam erat volutpat. Ut wisi enim ad minim veniam, quis nostrud exerci tationmcorper suscipit lobortis nisl ut aliquip ex ea commodo consequat. Duis autem vel eum iriure dolor in hendrerit in suscipit lobortis nisl ut aliquip ex ea commodo consequat. Duis autem vel eum iriure dolor in hendrerit in vulputate velit esse molestie consequat, vel illum</p>
      <p>Sorem ipsum dolor sit amet, consectetuer adipiscing elit, sed diam nonmmy nibh euismod tincidunt ut laor eet dolore magna aliquam erat volutpat. Ut wisi enim ad minim veniam, quis nostrud exerci tationmcorper suscipit lobortis nisl ut aliquip ex ea commodo consequat. Duis autem vel eum iriure dolor in</p>
    </section>

    <div class="closing">Sincerely,</div>
    <div class="signature">Marcus Ellery</div>
  </main>
</body>
</html>
```